Web Design Project

We need a web design for a new company. We have a logo, and we've identified the style of a website that we'd like to adapt (www.brindlemoor.com). We do not sell to the public. The purpose of the site is (1) to allow our appointed sales partners to log in to our proprietary database system and (2) to provide a basic web presence and some basic information about our company.

We sell business insurance through independent agents - our sales partners.

Please do not use a photo of a person/s as a central design element, or at all.

Target Market(s)

The purpose of the site is not to sell, but to provide a professional landing page for a log in and some basic company information.

Industry/Entity Type

Business

Requirements
Must have
• A professional look. Agent log in must be central, clear and easy. Use of our logo and our colors.
Should not have
• Photos of people

```html
<!DOCTYPE html>
<html lang="en">
<head>
<meta charset="utf-8">
<title>Harlow Bay Insurance</title>
<link rel="stylesheet" href="https://fonts.googleapis.com/css2?family=Ubuntu:ital,wght@0,400;0,500;0,700;1,400&family=Noto+Serif&display=swap">
<style>
:root{
  --navy:#08507a;
  --navy-dark:#0a3552;
  --orange:#f28a1a;
  --orange-dark:#d86f08;
  --text:#4a4a4a;
  --line:#cfcfcf;
  --hero:#e9e9e9;
  --footer:#ececec;
  --chip:#5f5f5f;
  --accent-grey:#6f8a9a;
}
*{box-sizing:border-box;margin:0;padding:0}
html,body{width:960px;height:1200px;overflow:hidden}
body{position:relative;background:#fff;font-family:"Ubuntu",sans-serif;color:var(--text);font-size:10px}
.abs{position:absolute}
h1,h2,h3{font-weight:400}

/* header */
.site-header{left:0;top:0;width:960px;height:102px;background:linear-gradient(#0c4a6f,var(--navy-dark))}
.utility-bar{left:490px;top:0;width:470px;height:31px;background:#fff;border-bottom-left-radius:18px 31px;display:flex;align-items:center;padding-left:26px;gap:5px;font-size:10px;color:var(--navy)}
.utility-bar .sep{color:#999}
.utility-bar .phone{font-size:13px;font-weight:500;color:#333}
.search{margin-left:9px;width:85px;height:18px;border:1px solid #bbb;border-radius:2px;background:#f2f2f2;font-style:italic;color:#aaa;font-size:9px;padding:3px 5px;position:relative}
.search svg{position:absolute;right:3px;top:2px}
.brand{left:104px;top:30px;display:flex;align-items:center;gap:8px;color:#fff;font-size:17px;font-weight:500}
.brand .mark{width:16px;height:16px;background:#fff}
.main-nav{left:352px;top:50px;display:flex;align-items:center;color:#fff;font-size:11.5px}
.main-nav span{padding:0 13px;border-left:1px solid #2e6a8f;line-height:18px}
.main-nav span:nth-child(2){border-left:0}
.main-nav .active{background:var(--orange);border:0;border-radius:13px;padding:4px 15px;line-height:17px}

/* hero */
.hero{left:0;top:102px;width:960px;height:358px;background:radial-gradient(ellipse at 50% 40%,#f3f3f3,var(--hero))}
.hero-title{left:106px;top:196px;font-size:34px;line-height:39px;color:var(--navy);white-space:nowrap}
.hero-title em{font-style:normal;color:var(--accent-grey)}
.hero-btn{left:103px;top:335px;width:194px;height:39px;background:linear-gradient(var(--orange),var(--orange-dark));border-radius:3px;color:#fff;font-size:15px;font-weight:500;display:flex;align-items:center;justify-content:center;box-shadow:0 1px 2px rgba(0,0,0,.3)}
.hero-art{left:412px;top:116px;width:444px;height:320px;border-radius:6px;background:radial-gradient(circle at 60% 35%,#6fd24a,#c9d8c3 55%,#e2e2e2 80%)}
.slider-dots{left:443px;top:434px;display:flex;gap:5px}
.slider-dots i{width:14px;height:14px;border-radius:50%;background:#6d8fa6}
.slider-dots i:first-child{background:var(--navy-dark)}

/* agent login */
.login{left:104px;top:493px;width:240px;height:221px;border:2px solid var(--navy);background:#f6f6f6;padding:10px 12px}
.panel-title{font-style:italic;font-size:19px;color:#555}
.login p{margin-top:6px;font-size:10px;line-height:14px;color:var(--navy)}
.learn{margin-top:6px;display:flex;align-items:center;gap:5px;color:#555}
.learn .dot{width:9px;height:9px;border-radius:50%;background:#e84c3d}
.learn em{color:var(--navy)}
.field{width:200px;height:25px;border:1px solid #bbb;border-radius:3px;background:#fff;padding:6px 9px;color:#777;font-size:10px}
.field.user{margin-top:19px}
.field.pass{margin-top:11px}
.login-row{margin-top:12px;display:flex;align-items:center;font-size:9px;color:#333;padding-left:13px}
.login-row svg{margin-left:24px}
.login-btn{margin-left:13px;width:65px;height:23px;background:var(--navy);color:#fff;border-radius:2px;font-size:11px;font-weight:500;display:flex;align-items:center;justify-content:center}

/* news */
.news{left:104px;top:728px;width:240px;height:318px;background:var(--navy);outline:1px solid #bbb;outline-offset:1px;padding:10px 12px;color:#fff}
.news .panel-title{color:#fff}
.news-list{margin-top:8px}
.news-item{display:flex;gap:12px;padding:8px 0 11px;border-bottom:1px solid #3a7aa0}
.news-item:first-child{padding-top:6px}
.news-item:last-child{border:0}
.date{width:58px;height:52px;flex:none;background:#fff;color:var(--navy-dark);font-family:"Noto Serif",serif;text-align:center;border-radius:2px}
.date b{display:block;font-weight:400;font-size:26px;line-height:32px}
.date small{display:block;font-size:13px;line-height:12px;color:#555}
.news-item p{font-size:9.5px;line-height:16px}
.news-item p a{font-style:italic;color:#f4c21b;font-size:8.5px;text-decoration:underline}
.read-all{left:0;top:286px;width:240px;text-align:center;font-size:10px;font-weight:500;text-decoration:underline}

/* lines of business */
.line-card{top:492px;width:110px;text-align:center}
.line-card .photo{margin:0 auto;width:102px;height:102px;border-radius:50%;border:3px solid #e8e8e8;box-shadow:0 0 0 1px #ccc}
.line-card h3{margin-top:9px;font-size:20px;line-height:23px;color:var(--navy)}
.chip{display:inline-block;margin-top:12px;background:var(--chip);color:#fff;font-size:10.5px;padding:3px 5px;border-radius:2px}

/* content */
.rule{height:1px;background:var(--line)}
.section-title{font-style:italic;font-size:18.5px;color:#444}
.welcome-art{left:360px;top:750px;width:166px;height:111px;border:1px solid #ddd;background:linear-gradient(120deg,#eef1f4,#c9d3dc 50%,#eef0f3)}
.body-text{font-size:10px;line-height:16px;color:#555}
.btn-navy{background:var(--navy);color:#fff;font-size:10.5px;font-weight:500;border-radius:2px;display:flex;align-items:center;justify-content:center}
.link-caps{font-size:10.5px;font-weight:500;color:var(--navy);text-decoration:underline}
.quote-mark{font-family:"Noto Serif",serif;font-weight:700;font-size:34px;line-height:24px;color:#999}
.testimonial{font-style:italic;font-size:10px;line-height:16px;color:#555}
.meta{font-style:italic;font-size:8.5px}

/* footer */
.site-footer{left:0;top:1060px;width:960px;height:140px;background:var(--footer)}
.copy{font-size:10px;color:#777}
.copy span{color:var(--navy)}
.social{left:664px;top:1085px;display:flex;gap:8px}
.social i{width:26px;height:26px;border-radius:3px}
.contact{left:666px;top:1130px;font-size:8.5px;line-height:14px;color:#666}
.contact b{display:block;font-size:11px;font-weight:500;color:#222;margin-bottom:2px}
</style>
</head>
<body>

<header class="site-header abs">
  <div class="utility-bar abs">
    <span>Agent Login</span><span class="sep">|</span><span>Register</span><span class="sep">|</span><span>Call Us :</span><span class="phone">555.014.2290</span>
    <div class="search">Search..
      <svg width="14" height="13" viewBox="0 0 14 13"><circle cx="5" cy="5" r="3.5" fill="none" stroke="#0a3552" stroke-width="1.8"/><line x1="7.5" y1="7.5" x2="12.5" y2="12" stroke="#0a3552" stroke-width="2.2"/></svg>
    </div>
  </div>
  <div class="brand abs"><i class="mark"></i>Harlow Bay Insurance</div>
  <nav class="main-nav abs">
    <span class="active">Home</span><span>About Us</span><span>Services</span><span>Products</span><span>Claim Center</span><span>Blog</span><span>Contact Us</span>
  </nav>
</header>

<section class="hero abs"></section>
<h1 class="hero-title abs">Sales <em>partners</em>, log<br>in to your agent<br>desk..</h1>
<div class="hero-btn abs">Partner Agent Login</div>
<div class="hero-art abs" role="img" aria-label="Illustration of a business building sheltered under a large green umbrella, wrapped in yellow insured tape"></div>
<div class="slider-dots abs"><i></i><i></i><i></i><i></i></div>

<section class="login abs">
  <h2 class="panel-title">Agent Login</h2>
  <p>Quote, bind and track business policies in the partner system.</p>
  <div class="learn"><i class="dot"></i>Learn more or <em>Register</em></div>
  <div class="field user">Agent ID</div>
  <div class="field pass">Password</div>
  <div class="login-row">Forgot Password ?
    <svg width="10" height="13" viewBox="0 0 10 13"><path d="M2.5 6V4a2.5 2.5 0 0 1 5 0v2" fill="none" stroke="#777" stroke-width="1.5"/><rect x="1" y="6" width="8" height="7" rx="1" fill="#777"/></svg>
    <span class="login-btn">Log In</span>
  </div>
</section>

<section class="news abs">
  <h2 class="panel-title">Latest News</h2>
  <div class="news-list">
    <div class="news-item"><div class="date"><b>28</b><small>Nov</small></div><p>Ut wisi enim ad minim veniam, quis nostrud exerci tation ulla-mcorper..... <a>Read More</a></p></div>
    <div class="news-item"><div class="date"><b>25</b><small>Nov</small></div><p>Ut wisi enim ad minim veniam, quis nostrud exerci tation ulla-mcorper..... <a>Read More</a></p></div>
    <div class="news-item"><div class="date"><b>20</b><small>Nov</small></div><p>Ut wisi enim ad minim veniam, quis nostrud exerci tation ulla-mcorper..... <a>Read More</a></p></div>
  </div>
  <div class="read-all abs">READ ALL NEWS</div>
</section>

<div class="line-card abs" style="left:361px"><div class="photo" role="img" aria-label="Photo of a commercial office building" style="background:linear-gradient(#7fb1e0 40%,#b9c2cb 41%,#8c98a4 85%)"></div><h3>Commercial<br>Property</h3><span class="chip">Read More</span></div>
<div class="line-card abs" style="left:488px"><div class="photo" role="img" aria-label="Photo of a shop front on a high street" style="background:linear-gradient(#c8d8e4,#b58a6a 60%,#7a7a7a)"></div><h3>General<br>Liability</h3><span class="chip">Read More</span></div>
<div class="line-card abs" style="left:617px"><div class="photo" role="img" aria-label="Photo of a fleet of delivery vans" style="background:linear-gradient(#9fc3de 35%,#e6e6e6 55%,#6d7680)"></div><h3>Commercial<br>Auto</h3><span class="chip">Read More</span></div>
<div class="line-card abs" style="left:744px"><div class="photo" role="img" aria-label="Photo of a warehouse interior with stacked goods" style="background:linear-gradient(#b4a58e 40%,#d98a3a 60%,#9a9a9a)"></div><h3>Workers'<br>Comp</h3><span class="chip">Read More</span></div>

<div class="rule abs" style="left:360px;top:702px;width:496px"></div>
<h2 class="section-title abs" style="left:360px;top:714px">Welcome to our Company !</h2>
<div class="welcome-art abs" role="img" aria-label="Photo of a modern office reception desk"></div>
<p class="body-text abs" style="left:544px;top:746px;width:312px">Lorem ipsum dolor sit amet, consectetur adipiscing elit. Fusce accumsan, elit a suscipit sagittis, tortor sapien cursus risus, non rhoncus lectus nunc ac nulla.<br>Aliquam molestie, mi et imperdiet euismod, dui purus auctor tellus, et interdum lacus lectus et ante.</p>
<div class="btn-navy abs" style="left:544px;top:838px;width:73px;height:23px">Read More</div>

<div class="rule abs" style="left:360px;top:886px;width:496px"></div>
<h2 class="section-title abs" style="left:360px;top:897px">What We Offer ?</h2>
<p class="body-text abs" style="left:360px;top:928px;width:232px">Lorem ipsum dolor sit amet, consectetur adipi&shy;scing elit. Fusce accumsan, elit a suscipit sagittis, tortor sapien cursus risus, non rhoncus lectus nunc ac nulla.<br>Vivamus egestas risus in magna varius commodo.</p>
<div class="link-caps abs" style="left:362px;top:1033px">READ MORE</div>
<div class="abs" style="left:608px;top:900px;width:1px;height:146px;background:var(--line)"></div>
<h2 class="section-title abs" style="left:630px;top:897px">Testimonials</h2>
<div class="quote-mark abs" style="left:630px;top:932px">&ldquo;</div>
<p class="testimonial abs" style="left:630px;top:931px;width:226px;text-indent:29px">Nam fermentum vestibulum purus id aliquet. Phasellus dui ante, ultricies et sollicitudin pretium, fermentum vel velit......</p>
<div class="meta abs" style="left:630px;top:993px;color:var(--navy)">Posted on Nov28, 2012</div>
<div class="meta abs" style="left:788px;top:993px;color:#333">By Lena Corvik</div>
<div class="link-caps abs" style="left:631px;top:1033px">READ ALL TESTIMONIALS</div>

<footer class="site-footer abs"></footer>
<div class="copy abs" style="left:104px;top:1091px">© 2012 <span>Harlow Bay Insurance</span> &nbsp; All Right Reserved &nbsp;| &nbsp;Privacy Policy</div>
<div class="copy abs" style="left:104px;top:1132px;font-size:9px">© 2012 <span>Harlow Bay Insurance</span> &nbsp; All Right Reserved &nbsp;| &nbsp;Privacy Policy</div>
<div class="social abs"><i style="background:#3a5f9e"></i><i style="background:#4fb6de"></i><i style="background:#f07a1c"></i></div>
<div class="contact abs"><b>1-800-555-0142</b>Mon-Fri 7am-1am EST, Sat 7am-11:30pm EST,<br>Sun 9am-10pm EST</div>

</body>
</html>
```